Single-sided business card for restaurant velmora with new logo made on this site

Business card options with new logo including restaurant name, address, phone number and website. This business card is single-sided only and will be presented at the hostess desk for clients to take. I would like to see options based on a cream card background, a white card background, a yellow card background and a burgundy colored background. It needs to be elegant and traditional.

Target Market(s)

local and international crowd

Industry/Entity Type

restaurant

Contact Information for Business Card

address, website and phone number

Font styles to use
Serif

Colors
EE7325
F08F49
F5BC92
FAE3D3
FDF4ED

Requirements
Must have
• new logo, address, phone number, website
Should not have
• more than three colors

```html
<!DOCTYPE html>
<html lang="es">
<head>
<meta charset="utf-8">
<title>Velmora — Tarjeta de presentación</title>
<link rel="stylesheet" href="https://fonts.googleapis.com/css2?family=Cinzel:wght@400;600;700&display=swap">
<style>
  :root {
    --backdrop: #d6d6d6;
    --card: #ffffff;
    --ink: #3a1a1c;
    --marigold: #f2b12f;
    --rule-fade: rgba(58, 26, 28, 0);
  }
  * { margin: 0; padding: 0; box-sizing: border-box; }
  html, body {
    width: 1200px;
    height: 1200px;
    overflow: hidden;
    background: var(--backdrop);
  }
  .business-card {
    position: absolute;
    left: 263px;
    top: 50px;
    width: 673px;
    height: 1100px;
    background: var(--card);
    border: 1px solid var(--ink);
    color: var(--ink);
    font-family: "Cinzel", serif;
    text-align: center;
  }
  .brand-square {
    position: absolute;
    left: 232px;
    top: 161px;
    width: 211px;
    height: 213px;
    background: var(--marigold);
  }
  .brand-name {
    position: absolute;
    left: 0;
    right: 0;
    top: 410px;
    font-size: 66px;
    font-weight: 600;
    letter-spacing: 0.14em;
    padding-left: 0.14em;
    line-height: 1;
  }
  .reservations-label {
    position: absolute;
    left: 0; right: 0;
    top: 644px;
    font-size: 38px;
    font-weight: 700;
    letter-spacing: 0.02em;
    line-height: 1;
  }
  .reservations-phone {
    position: absolute;
    left: 0; right: 0;
    top: 692px;
    font-size: 52px;
    font-weight: 600;
    line-height: 1;
  }
  .divider {
    position: absolute;
    left: 180px;
    width: 311px;
    height: 2px;
    background: linear-gradient(to right, var(--ink) 0%, var(--ink) 55%, var(--rule-fade) 100%);
  }
  .divider--upper { top: 766px; }
  .divider--lower { top: 979px; }
  .address {
    position: absolute;
    left: 0; right: 0;
    top: 798px;
    font-style: normal;
    font-size: 34px;
    font-weight: 400;
    letter-spacing: 0.05em;
    line-height: 40.5px;
  }
  .website {
    position: absolute;
    left: 0; right: 0;
    top: 1006px;
    font-size: 32px;
    letter-spacing: 0.04em;
    line-height: 1;
  }
</style>
</head>
<body>
  <main class="business-card">
    <div class="brand-square"></div>
    <h1 class="brand-name">VELMORA</h1>

    <p class="reservations-label">RESERVACIONES</p>
    <p class="reservations-phone">958-555-0142</p>

    <div class="divider divider--upper"></div>

    <address class="address">
      Restaurant Velmora<br>
      Jacaranda 415<br>
      Bahías de Santa Lucía<br>
      Oaxaca CP 70940
    </address>

    <div class="divider divider--lower"></div>

    <p class="website">WWW.VELMORA.COM.MX</p>
  </main>
</body>
</html>
```